Classy, Elegant, Simple Business Card Design

Looking to have a classy, simple, and elegant design. Want a top notch designed business card. I really like the look of the new torvane credit card. I also like the design I attached. I am trying to reach 21-29 year old females for booking us for there wedding or event. We offer Disc Jockey Service, Photo Booth Rentals, and Uplighting .

Target Market(s)

21-28 year old females

Contact Information for Business Card

Has to have logo, website, email, and phone number

Font styles to use
Other font styles liked:
• open to font choice, modern, clean
Designer to choose
33a6d7
0791cd
0555a3
ffffff

Requirements
Must have
• Has to have logo, website, email, and phone number
Nice to have
• I really like the design of the new torvane credit card. I also included my logo and some designs I like
Should not have
• clutter or too much info

```html
<!DOCTYPE html>
<html lang="en">
<head>
<meta charset="utf-8">
<title>Tidelight Event Group – Business Card</title>
<link href="https://fonts.googleapis.com/css2?family=Poppins:wght@400;500;600&display=swap" rel="stylesheet">
<style>
  :root {
    --stage: #1e1e1e;
    --card-front: #ffffff;
    --card-back-top: #b6b6b6;
    --card-back-bottom: #acacac;
    --brand-blue: #0791cd;
    --brand-deep: #0555a3;
    --text-dark: #3a3a3a;
    --text-muted: #9a9a9a;
    --divider: #8a8a8a;
    --white: #ffffff;
  }
  * { margin: 0; padding: 0; box-sizing: border-box; }
  html, body { width: 1200px; height: 1200px; overflow: hidden; }
  body {
    background: var(--stage);
    font-family: "Poppins", sans-serif;
    position: relative;
  }
  .card {
    position: absolute;
    left: 262px;
    width: 686px;
    height: 392px;
    box-shadow: 0 18px 30px rgba(0,0,0,0.55);
  }
  .card-front { top: 165px; background: var(--card-front); }
  .card-back {
    top: 653px;
    background: linear-gradient(180deg, var(--card-back-top), var(--card-back-bottom));
  }

  .brand {
    position: absolute;
    left: 118px;
    top: 140px;
    width: 172px;
    text-align: center;
    color: var(--brand-deep);
    font-weight: 500;
  }
  .brand-dot {
    display: block;
    width: 34px; height: 34px;
    border-radius: 50%;
    background: var(--brand-deep);
    margin: 0 auto 12px;
  }
  .brand-name { font-size: 25px; line-height: 1; letter-spacing: 0.5px; }
  .brand-sub { font-size: 10px; letter-spacing: 5px; margin-top: 6px; }

  .divider {
    position: absolute;
    left: 319px; top: 132px;
    width: 1.5px; height: 127px;
    background: var(--divider);
  }

  .person { position: absolute; left: 347px; top: 130px; }
  .person-name {
    color: var(--brand-blue);
    font-size: 23px; font-weight: 500; line-height: 1.2;
  }
  .person-title {
    color: var(--text-muted);
    font-size: 15.5px; line-height: 1.2;
  }
  .contact-list { list-style: none; margin-top: 14px; }
  .contact-list li {
    display: flex; align-items: center; gap: 8px;
    color: var(--text-dark);
    font-size: 15.5px; line-height: 20px;
  }
  .contact-list svg { width: 12px; height: 12px; fill: var(--brand-blue); flex: none; }

  .back-name {
    position: absolute;
    left: 0; right: 0; top: 130px;
    text-align: center;
    color: var(--brand-blue);
    font-size: 64px; font-weight: 600; letter-spacing: 1px;
  }
  .services {
    position: absolute;
    left: 0; right: 0; top: 336px;
    text-align: center;
    color: var(--white);
    font-size: 15.5px; font-weight: 500;
  }
</style>
</head>
<body>
  <section class="card card-front">
    <div class="brand">
      <span class="brand-dot"></span>
      <div class="brand-name">TIDELIGHT</div>
      <div class="brand-sub">EVENT GROUP</div>
    </div>
    <div class="divider"></div>
    <div class="person">
      <div class="person-name">Daniel Reyes</div>
      <div class="person-title">President</div>
      <ul class="contact-list">
        <li>
          <svg viewBox="0 0 24 24" aria-hidden="true"><path d="M6.6 10.8c1.4 2.8 3.8 5.1 6.6 6.6l2.2-2.2c.3-.3.7-.4 1-.2 1.1.4 2.3.6 3.6.6.6 0 1 .4 1 1V20c0 .6-.4 1-1 1C10.6 21 3 13.4 3 4c0-.6.4-1 1-1h3.5c.6 0 1 .4 1 1 0 1.3.2 2.5.6 3.6.1.3 0 .7-.2 1z"/></svg>
          555-014-2870
        </li>
        <li>
          <svg viewBox="0 0 24 24" aria-hidden="true"><path d="M2 5h20v14H2z M4 7v.4l8 5 8-5V7z" fill-rule="evenodd"/></svg>
          info@tidelightgroup.com
        </li>
        <li>
          <svg viewBox="0 0 24 24" aria-hidden="true"><circle cx="12" cy="12" r="10"/><path d="M2 12h20M12 2c3 3 3 17 0 20M12 2c-3 3-3 17 0 20" stroke="#fff" stroke-width="1.5" fill="none"/></svg>
          www.tidelightgroup.com
        </li>
      </ul>
    </div>
  </section>

  <section class="card card-back">
    <div class="back-name">TIDELIGHT</div>
    <p class="services">Disc Jockey Service • Photo Booth Rentals • Uplighting .</p>
  </section>
</body>
</html>
```